Building company buisness cards

We are looking for a sharp modern new look for our business cards.
We are a New Zealand based company that specialises in house and land packages.
We have attached a photo of the current logo and would like to see if it can be improved somehow if needed.
We are open to any colours but we have chosen green at this stage.
Feel free to change the font and make the logo smarter looking.
Play with the colours and see what looks best.

We want a card that looks so good know one will want to throw it away!

Target Market(s)

Home buyers

Industry/Entity Type

Building

Contact Information for Business Card

Derek Tolvane
0217394062
dtolvane@quillmarkhomesteads.co.nz
quillmarkhomesteads.co.nz

Font styles to use
Serif
Sans Serif

Colors

Designer to choose colors to be used in the design.

Requirements
Must have
• Logo and company name on one side, details on the other side
Nice to have
• Color codes for the original green are HEX #4a8028, RGB(74,128,40), CMYK(42,0,69,50)
• Round corners, Raised and/or spot UV

```html
<!DOCTYPE html>
<html lang="en">
<head>
<meta charset="utf-8">
<title>Quillmark Homesteads – Business Cards</title>
<link rel="stylesheet" href="https://fonts.googleapis.com/css2?family=Open+Sans:wght@400;600;800&display=swap">
<style>
  :root {
    --backdrop: #1c1c1c;
    --card-green: #4a8028;
    --ink-white: #ffffff;
    --rule-soft: rgba(255, 255, 255, 0.35);
  }
  * { margin: 0; padding: 0; box-sizing: border-box; }
  html, body {
    width: 1200px;
    height: 900px;
    overflow: hidden;
    background: var(--backdrop);
    font-family: "Open Sans", Arial, sans-serif;
    color: var(--ink-white);
  }
  .canvas {
    position: relative;
    width: 1200px;
    height: 900px;
  }
  .card {
    position: absolute;
    left: 320px;
    width: 560px;
    height: 320px;
    background: var(--card-green);
    border-radius: 26px;
    overflow: hidden;
  }
  .card--logo-side { top: 100px; }
  .card--details-side { top: 480px; }

  /* Logo side */
  .logo-side__name {
    position: absolute;
    left: 0;
    right: 0;
    top: 100px;
    text-align: center;
    font-weight: 800;
    font-size: 40px;
    line-height: 1.05;
    letter-spacing: -0.5px;
  }
  .logo-side__web {
    position: absolute;
    right: 40px;
    bottom: 34px;
    font-size: 13px;
    font-weight: 400;
    letter-spacing: 0.2px;
  }

  /* Details side */
  .brand {
    position: absolute;
    left: 260px;
    top: 58px;
    width: 270px;
    text-align: center;
  }
  .brand__name {
    font-weight: 800;
    font-size: 32px;
    line-height: 1.02;
    letter-spacing: -0.4px;
  }
  .brand__rule {
    width: 70px;
    height: 1px;
    margin: 12px auto 0;
    background: var(--rule-soft);
  }
  .contact {
    position: absolute;
    left: 38px;
    bottom: 30px;
  }
  .contact__person {
    font-weight: 600;
    font-size: 19px;
    text-transform: uppercase;
    margin-bottom: 12px;
    letter-spacing: 0.2px;
  }
  .contact__list { list-style: none; }
  .contact__item {
    display: flex;
    align-items: center;
    gap: 8px;
    font-size: 16px;
    line-height: 22px;
  }
  .contact__icon { width: 12px; height: 12px; flex: none; }
</style>
</head>
<body>
<main class="canvas">

  <section class="card card--logo-side" aria-label="Card front with company name">
    <p class="logo-side__name">quillmark<br>homesteads.</p>
    <p class="logo-side__web">www.quillmarkhomesteads.co.nz</p>
  </section>

  <section class="card card--details-side" aria-label="Card back with contact details">
    <div class="brand">
      <p class="brand__name">quillmark<br>homesteads.</p>
      <div class="brand__rule"></div>
    </div>

    <div class="contact">
      <p class="contact__person">Derek Tolvane</p>
      <ul class="contact__list">
        <li class="contact__item">
          <svg class="contact__icon" viewBox="0 0 12 12" aria-hidden="true">
            <path fill="#fff" d="M1 4.5C1 3 2.5 2 6 2s5 1 5 2.5V5.5H8.5V4.3h-5v1.2H1z"/>
            <rect fill="#fff" x="2.5" y="6" width="7" height="4.5" rx="0.8"/>
          </svg>
          0217394062
        </li>
        <li class="contact__item">
          <svg class="contact__icon" viewBox="0 0 12 12" aria-hidden="true">
            <rect fill="#fff" x="0.5" y="2.5" width="11" height="7.5" rx="0.8"/>
            <path fill="none" stroke="#4a8028" stroke-width="1" d="M1 3l5 4 5-4"/>
          </svg>
          dtolvane@quillmarkhomesteads.co.nz
        </li>
        <li class="contact__item">
          <svg class="contact__icon" viewBox="0 0 12 12" aria-hidden="true">
            <circle fill="#fff" cx="6" cy="6" r="5.5"/>
            <path fill="none" stroke="#4a8028" stroke-width="0.9" d="M0.5 6h11M6 0.5c-2.5 3-2.5 8 0 11M6 0.5c2.5 3 2.5 8 0 11"/>
          </svg>
          www.quillmarkhomesteads.co.nz
        </li>
      </ul>
    </div>
  </section>

</main>
</body>
</html>
```